RTavenor Business Cards & Letterhead

I have a logo but need a design for some new business cards. We are a Design-Build Firm that specializes in the design and construction of commercial projects.
the cards need to be professional. no cartoon stuff.
i would like to have the cards in AI format so I can update the card as needed. Logo is provided.
Our Address is: 4187 Marlowe Ct. Apex, North Carolina 27614

```html
<!DOCTYPE html>
<html lang="en">
<head>
<meta charset="utf-8">
<title>RTavenor Business Card</title>
<link href="https://fonts.googleapis.com/css2?family=Open+Sans:wght@400;600;800&display=swap" rel="stylesheet">
<style>
  :root {
    --stage: #e4e2df;
    --card: #202125;
    --card-deep: #16171a;
    --logo-grey: #8b8d92;
    --brand-blue: #1d78c1;
    --band-blue-dark: #0f4f86;
    --text-light: #f2f3f5;
    --divider: #5a5c62;
  }
  * { margin: 0; padding: 0; box-sizing: border-box; }
  html, body {
    width: 1200px; height: 780px; overflow: hidden;
    background: var(--stage);
    font-family: "Open Sans", Arial, sans-serif;
  }
  .sheet {
    position: relative; width: 1200px; height: 780px;
    display: flex; align-items: center; justify-content: center; gap: 40px;
  }
  .card {
    position: relative; width: 540px; height: 309px;
    background: var(--card); overflow: hidden;
    box-shadow: 0 6px 18px rgba(0,0,0,.25);
  }
  /* front */
  .logo {
    position: absolute; display: flex; align-items: center; gap: 10px;
    color: var(--logo-grey); font-weight: 800; letter-spacing: 1px;
  }
  .logo-mark { background: var(--brand-blue); }
  .logo-reg { font-size: 11px; font-weight: 400; align-self: flex-end; margin-bottom: 6px; }
  .card-front .logo { left: 150px; top: 52px; font-size: 46px; }
  .card-front .logo-mark { width: 30px; height: 30px; }
  .identity { position: absolute; left: 36px; top: 150px; width: 190px; text-align: right; }
  .identity-name { color: var(--brand-blue); font-weight: 600; font-size: 19px; letter-spacing: .5px; text-transform: uppercase; }
  .identity-role { color: var(--text-light); font-size: 12px; margin-top: 2px; }
  .divider { position: absolute; left: 248px; top: 145px; width: 1px; height: 72px; background: var(--divider); }
  .contact { position: absolute; left: 268px; top: 148px; list-style: none; }
  .contact li { display: flex; align-items: center; gap: 8px; color: var(--text-light); font-size: 13px; line-height: 22px; }
  .contact svg { width: 12px; height: 12px; flex: none; }
  .address-band {
    position: absolute; left: 0; right: 0; bottom: 32px; height: 28px;
    background: linear-gradient(90deg, var(--brand-blue), var(--band-blue-dark));
    color: var(--text-light); font-size: 13.5px; line-height: 28px; padding-left: 36px;
  }
  /* back */
  .back-pattern {
    position: absolute; inset: 0;
    background: linear-gradient(115deg, var(--card-deep) 0%, #1c1d20 45%, #4a4b4f 72%, #9d9ea2 100%);
  }
  .card-back .logo { left: 50%; top: 50%; transform: translate(-50%, -50%); font-size: 38px; }
  .card-back .logo-mark { width: 24px; height: 24px; }
</style>
</head>
<body>
<main class="sheet">
  <section class="card card-front">
    <div class="logo"><span class="logo-mark"></span><span>RTAVENOR</span><span class="logo-reg">®</span></div>
    <div class="identity">
      <p class="identity-name">Reid Tavenor</p>
      <p class="identity-role">Founder/President</p>
    </div>
    <div class="divider"></div>
    <ul class="contact">
      <li>
        <svg viewBox="0 0 12 12"><circle cx="6" cy="6" r="6" fill="#1d78c1"/><path d="M4 3l1 1.6-.7.8a4 4 0 0 0 2.3 2.3l.8-.7L9 8l-.6 1A5 5 0 0 1 3 3.6z" fill="#fff"/></svg>
        (919) 555-0148
      </li>
      <li>
        <svg viewBox="0 0 12 12"><circle cx="6" cy="6" r="6" fill="#1d78c1"/><circle cx="6" cy="6" r="3.3" fill="none" stroke="#fff" stroke-width=".8"/><path d="M2.7 6h6.6M6 2.7v6.6" stroke="#fff" stroke-width=".7"/></svg>
        www.rtavenor.com
      </li>
      <li>
        <svg viewBox="0 0 12 12"><circle cx="6" cy="6" r="6" fill="#1d78c1"/><rect x="3" y="4" width="6" height="4.2" fill="none" stroke="#fff" stroke-width=".8"/><path d="M3 4l3 2.3L9 4" fill="none" stroke="#fff" stroke-width=".8"/></svg>
        RT@RTavenor.com
      </li>
    </ul>
    <div class="address-band">4187 Marlowe Ct. Apex, North Carolina 27614</div>
  </section>

  <section class="card card-back">
    <div class="back-pattern" role="img" aria-label="Repeating brand-mark pattern on black with a glossy silver sheen"></div>
    <div class="logo"><span class="logo-mark"></span><span>RTAVENOR</span><span class="logo-reg">®</span></div>
  </section>
</main>
</body>
</html>
```